Media Services Start-up -- Corporate Website and Logo Design. Inspiration required!

We need a logo design and corporate website design, including coding, for our start-up business.
Vennatra’s value proposition is based on bringing together media content from a vast number of geographies globally, adding human and AI curation, translation and editing, and delivering the content using tailored customer interfaces. On the one hand, the business brings together media coverage from all over the world, and on the other it brings together content, human skills and technology to deliver a supreme customer experience.
Vennatra is a B2B media monitoring and analytics business with emphasis on global customers. Vennatra's service offering is centred around sourcing media content from different markets, processing, storing and delivering the content and insights derived from it using an online platform / mobile app.
The messaging we want to create through the logo is:
- Global scope
- Speed of delivery
- Cost-efficiency
- Multi-lingual
- Tailor-made
- Trustworthy
Target Market(s)
Business to business, PR / Communications, Media, Marketing
Logo Text
Vennatra
Coding
Coded - Design and coding required
Number of Pages Required
5+ page
Font styles to use
Other font styles liked:
- See Design Brief for details
Colors
Designer to choose colors to be used in the design.

```html
<!DOCTYPE html>
<html lang="en">
<head>
<meta charset="utf-8">
<title>Vennatra — Global Media Intelligence</title>
<link href="https://fonts.googleapis.com/css2?family=Roboto:wght@400;500;700;900&display=swap" rel="stylesheet">
<style>
  :root{
    --ink:#0b0e16;
    --night:#111827;
    --navy:#1b2a4a;
    --glow:#3f6fc0;
    --white:#ffffff;
    --field:#4a4d53;
    --panel-edge:#d4d5d8;
    --accent:#0a6fd6;
    --accent-dark:#085fb8;
    --text-dark:#1a1a1a;
  }
  *{box-sizing:border-box;margin:0;padding:0}
  html,body{width:1200px;height:544px;overflow:hidden;background:var(--white)}
  body{font-family:"Roboto",Arial,sans-serif;color:var(--white);position:relative}

  .hero{position:absolute;left:0;top:0;width:1200px;height:508px;overflow:hidden;background:var(--ink)}
  .hero-photo{position:absolute;inset:0;
    background:
      radial-gradient(ellipse 260px 140px at 560px 500px, rgba(90,150,240,.75), transparent 70%),
      radial-gradient(ellipse 420px 300px at 600px 330px, rgba(40,70,130,.55), transparent 75%),
      linear-gradient(180deg,#07090e 0%,#121a2c 45%,#16223c 100%);}
  .hero-cluster{position:absolute;left:494px;top:85px;width:262px;height:296px;border-radius:10px;
    background:radial-gradient(ellipse at 55% 45%, rgba(160,120,220,.55), rgba(80,170,120,.35) 45%, rgba(60,150,220,.15) 75%, transparent 100%);}

  .site-header{position:absolute;left:140px;top:0;width:918px;height:80px}
  .brand{position:absolute;left:0;top:13px;font-size:42px;font-weight:700;letter-spacing:-.5px;color:#e8e8e8}
  .contact{position:absolute;top:30px;font-size:14.5px;display:flex;align-items:center;gap:6px}
  .contact.phone{left:477px}
  .contact.mail{left:614px}
  .signin{position:absolute;left:779px;top:25px;width:96px;height:32px;border:1px solid #cfcfcf;display:flex}
  .signin .edit{width:31px;border-right:1px solid #cfcfcf;display:flex;align-items:center;justify-content:center}
  .signin span{flex:1;display:flex;align-items:center;justify-content:center;font-size:14.5px}
  .menu{position:absolute;left:886px;top:25px;width:32px;height:32px;border:1px solid #e0e0e0;display:flex;flex-direction:column;justify-content:center;align-items:center;gap:4px}
  .menu i{display:block;width:21px;height:3px;background:var(--white)}

  .intro{position:absolute;left:140px;top:165px;width:350px}
  .intro h1{font-size:32px;font-weight:700;line-height:38px;letter-spacing:.2px}
  .intro p{margin-top:14px;font-size:15.5px;line-height:24.7px;letter-spacing:.2px}
  .cta{position:absolute;left:140px;top:371px}
  .cta .frame{position:absolute;left:6px;top:5px;width:175px;height:39px;border:1px solid #9aa0a8}
  .cta a{position:relative;display:block;width:175px;height:39px;background:var(--accent);color:var(--white);
    text-decoration:none;font-size:15.5px;line-height:39px;text-align:center;letter-spacing:.2px}

  .lead-panel{position:absolute;left:753px;top:125px;width:304px;height:338px;border:7px solid var(--panel-edge);background:rgba(10,11,14,.93)}
  .lead-panel h2{position:absolute;left:14px;top:31px;font-size:21px;font-weight:700;white-space:nowrap}
  .field{position:absolute;left:12px;width:264px;height:42px;background:var(--field);display:flex;align-items:center;padding-left:10px;gap:7px;font-size:12.5px;color:#f1f1f1}
  .field.name{top:78px}
  .field.email{top:135px}
  .field.phone{top:192px}
  .submit{position:absolute;left:12px;top:249px;width:264px;height:43px;background:var(--accent);color:var(--white);border:0;
    font-family:"Roboto",Arial,sans-serif;font-size:17px;font-weight:700;letter-spacing:.3px}

  .site-footer{position:absolute;left:0;top:508px;width:1200px;height:36px;background:var(--white);color:var(--text-dark)}
  .site-footer small{position:absolute;left:141px;top:11px;font-size:13px}
  .social{position:absolute;left:998px;top:11px;display:flex;gap:10px}
  .social i{display:block;width:14px;height:14px;border-radius:50%;background:var(--text-dark)}
</style>
</head>
<body>
<section class="hero">
  <div class="hero-photo" role="img" aria-label="Background photo of a business hand touching a glowing tablet with silhouettes of people shaking hands"></div>
  <div class="hero-cluster" role="img" aria-label="Illustration of colourful app and social media icons rising from the tablet"></div>

  <header class="site-header">
    <div class="brand">Vennatra</div>
    <div class="contact phone">
      <svg width="14" height="14" viewBox="0 0 24 24"><path fill="#fff" d="M6.6 10.8a15.1 15.1 0 0 0 6.6 6.6l2.2-2.2c.3-.3.7-.4 1-.2 1.1.4 2.3.6 3.6.6.6 0 1 .4 1 1V20c0 .6-.4 1-1 1A17 17 0 0 1 3 4c0-.6.4-1 1-1h3.5c.6 0 1 .4 1 1 0 1.3.2 2.5.6 3.6.1.3 0 .7-.2 1l-2.3 2.2z"/></svg>
      +1 555 014 2290
    </div>
    <div class="contact mail">
      <svg width="20" height="14" viewBox="0 0 20 14"><rect x="0.8" y="0.8" width="18.4" height="12.4" fill="none" stroke="#fff" stroke-width="1.6"/><path d="M1 1l9 7 9-7M1 13l6.5-6M19 13l-6.5-6" fill="none" stroke="#fff" stroke-width="1.6"/></svg>
      info@vennatra.com
    </div>
    <div class="signin">
      <div class="edit"><svg width="14" height="14" viewBox="0 0 16 16"><path d="M2 3h6M2 3v11h11V8" fill="none" stroke="#fff" stroke-width="1.6"/><path d="M6 10l1-3 6-6 2 2-6 6z" fill="#fff"/></svg></div>
      <span>Sign In</span>
    </div>
    <div class="menu"><i></i><i></i><i></i></div>
  </header>

  <div class="intro">
    <h1>DELIVERING GLOBAL MEDIA INTELLIGENCE</h1>
    <p>Vennatra is an international media intelligence service provider. We help communications teams build and operate truly global media monitoring and measurement programmes.</p>
  </div>
  <div class="cta"><span class="frame"></span><a href="#">CONTACT US TODAY</a></div>

  <form class="lead-panel">
    <h2>Learn More About Vennatra</h2>
    <label class="field name">
      <svg width="14" height="14" viewBox="0 0 16 16"><circle cx="8" cy="4.5" r="3.5" fill="#fff"/><path d="M1 16c0-4 3-6.5 7-6.5s7 2.5 7 6.5z" fill="#fff"/></svg>
      Your Name*
    </label>
    <label class="field email">
      <svg width="15" height="11" viewBox="0 0 20 14"><rect x="0.8" y="0.8" width="18.4" height="12.4" fill="none" stroke="#fff" stroke-width="1.6"/><path d="M1 1l9 7 9-7M1 13l6.5-6M19 13l-6.5-6" fill="none" stroke="#fff" stroke-width="1.6"/></svg>
      Your Email*
    </label>
    <label class="field phone">
      <svg width="14" height="14" viewBox="0 0 24 24"><path fill="#fff" d="M6.6 10.8a15.1 15.1 0 0 0 6.6 6.6l2.2-2.2c.3-.3.7-.4 1-.2 1.1.4 2.3.6 3.6.6.6 0 1 .4 1 1V20c0 .6-.4 1-1 1A17 17 0 0 1 3 4c0-.6.4-1 1-1h3.5c.6 0 1 .4 1 1 0 1.3.2 2.5.6 3.6.1.3 0 .7-.2 1l-2.3 2.2z"/></svg>
      Your Phone*
    </label>
    <button type="button" class="submit">GET STARTED</button>
  </form>
</section>

<footer class="site-footer">
  <small>Copyright © 2019 Vennatra. All Rights Reserved.</small>
  <div class="social" aria-label="Social links"><i></i><i></i><i></i></div>
</footer>
</body>
</html>
```